Bolts & Burdens: Mending What Lies Beneath

AUTHORS BIO:
Wade Pemberton is a 20-year Northern Union Aerial Corps veteran who served as a Crew Chief for K-37 and K-48 fighter jets, maintaining the backbone of America’s air superiority through multiple deployments to Afghanistan and other austere locations. Shaped by the loss of his father as a young adult and the lingering scars of childhood trauma, he confronts PTSD with the same tenacity he brought to the flightline. A survivor and advocate, he brings a raw, hard-earned perspective to "Bolts and Burdens," blending the grit of a serviceman with the insight of a man determined to heal. Focused on helping men confront their pain and find strength in vulnerability. Wade now lives in Jacksonville, North Carolina, where he continues to advocate for those shaped by trauma’s lasting weight.

SUMMARY:
In this raw and revealing non-fiction work, Wade Pemberton delves into the lasting echoes of childhood trauma and its profound impact on adult life, with a lens on his 20-year career in the Aerial Corps. Blending personal experience with hard-earned insight, the book explores how post-traumatic stress disorder (PTSD) shapes the mind and body, often in ways that remain hidden until the pressure builds beyond breaking points. With a focus on men—who are too often taught to bury their pain—this narrative offers a roadmap to understanding, confronting, and healing from the torque of trauma. Written in a direct, unflinching voice, "Bolts and Burdens" is both a memoir of resilience and a call to action for those ready to face the past to reclaim their future. Thank you for joining me on this adventure called life. It means more to me than you will ever know.

Target Market(s)

Those serving in the military and post military life with an emphasis on trauma

Font styles to use
Serif

Requirements
Must have
• NUAC K-37 or K-48 aircraft, NO AI GENERATED AIRCRAFT please
Nice to have
• An American Flag
Should not have
• AI generated aircraft

```html
<!DOCTYPE html>
<html lang="en">
<head>
<meta charset="utf-8">
<title>Bolts &amp; Burdens — Book Cover Wrap</title>
<link rel="stylesheet" href="https://fonts.googleapis.com/css2?family=Anton&family=Barlow+Condensed:wght@500&family=Lato:wght@400&family=Montserrat:wght@500&display=swap">
<style>
  :root {
    --page-bg: #f2f2f2;
    --cover-blue: #3d95e3;
    --cover-blue-deep: #2f7fd0;
    --ink-navy: #241f2e;
    --title-red: #cc1f30;
    --band-black: #0d0d0f;
    --paper-white: #ffffff;
    --body-ink: #1a2440;
    --sky-top: #7fb6e8;
    --sky-low: #cfe1ef;
    --tarmac: #7b7f86;
  }
  * { box-sizing: border-box; margin: 0; padding: 0; }
  html, body { width: 1200px; height: 1010px; overflow: hidden; background: var(--page-bg); }
  .wrap {
    position: absolute; left: 48px; top: 45px;
    display: flex; height: 920px;
    box-shadow: 0 8px 30px rgba(0,0,0,.18);
  }
  .cover, .spine { position: relative; height: 100%; background: var(--cover-blue); overflow: hidden; }
  .cover { width: 520px; }
  .spine { width: 64px; border-left: 1px solid rgba(0,0,0,.12); border-right: 1px solid rgba(0,0,0,.12); }
  .band {
    position: absolute; left: 0; right: 0; bottom: 0; height: 90px;
    background: var(--band-black);
  }
  .flag-haze {
    position: absolute; left: 0; right: 0;
    background: linear-gradient(120deg, rgba(255,255,255,.22), rgba(255,255,255,0) 55%, rgba(255,255,255,.12));
  }

  /* back cover */
  .back .flag-haze { top: 0; height: 210px; }
  .back-title { position: absolute; left: 160px; top: 40px; width: 170px; height: 130px; }
  .back-jet {
    position: absolute; left: 330px; top: 40px; width: 175px; height: 150px;
    background: linear-gradient(180deg, rgba(255,255,255,.18), rgba(60,70,90,.25));
    border-radius: 6px;
  }
  .back-blurb {
    position: absolute; left: 28px; top: 200px; width: 464px;
    font: 400 13.4px/1.38 "Lato", sans-serif; color: var(--body-ink); text-align: justify;
  }
  .byline {
    position: absolute; left: 28px; top: 420px; width: 464px;
    display: flex; align-items: center; gap: 16px;
    font: 500 22px/1 "Montserrat", sans-serif; color: var(--paper-white); white-space: nowrap;
  }
  .byline::before, .byline::after {
    content: ""; flex: 1; height: 2px;
    background: linear-gradient(90deg, var(--ink-navy), var(--title-red));
  }
  .portrait {
    position: absolute; left: 28px; top: 468px; width: 172px; height: 250px;
    background: linear-gradient(135deg, #c9373f 0%, #8fb4d9 35%, #6d95c4 70%, #1d2a4a 100%);
  }
  .bio {
    position: absolute; left: 214px; top: 466px; width: 278px;
    font: 400 13.4px/1.38 "Lato", sans-serif; color: var(--body-ink); text-align: justify;
  }

  /* spine */
  .spine-title, .spine-author {
    position: absolute; left: 50%; writing-mode: vertical-rl; transform: translateX(-50%);
    white-space: nowrap;
  }
  .spine-title { top: 36px; font: 400 38px/1 "Anton", sans-serif; color: var(--ink-navy); }
  .spine-title .red { color: var(--title-red); }
  .spine-author { top: 500px; font: 500 28px/1 "Montserrat", sans-serif; color: var(--paper-white); letter-spacing: 2px; }

  /* front cover */
  .front .flag-haze { top: 420px; height: 150px; }
  .front-title { position: absolute; left: 20px; top: 30px; width: 485px; height: 340px; }
  .subtitle {
    position: absolute; left: 40px; right: 20px; top: 380px;
    font: 500 36px/1 "Barlow Condensed", sans-serif; color: var(--paper-white);
    text-align: right; letter-spacing: .3px; white-space: nowrap;
  }
  .hero-jet {
    position: absolute; left: 0; right: 0; top: 470px; bottom: 90px;
    background: linear-gradient(180deg, rgba(61,149,227,0) 0%, var(--sky-top) 30%, var(--sky-low) 70%, var(--tarmac) 78%, #5f636a 100%);
  }
  .front-author {
    position: absolute; left: 0; right: 0; bottom: 0; height: 90px;
    display: flex; align-items: center; justify-content: center;
    font: 500 36px/1 "Montserrat", sans-serif; color: var(--paper-white); letter-spacing: 1px;
  }
</style>
</head>
<body>
<div class="wrap">

  <section class="cover back">
    <div class="flag-haze" role="img" aria-label="Faint waving national flag"></div>
    <div class="back-jet" role="img" aria-label="Faded rear view of a K-37 fighter jet on the flightline"></div>
    <svg class="back-title" viewBox="0 0 170 130" aria-label="Bolts &amp; Burdens">
      <defs>
        <linearGradient id="backRed" x1="0" y1="0" x2="0" y2="1">
          <stop offset="0" stop-color="#3a1f33"/><stop offset="1" stop-color="#cc1f30"/>
        </linearGradient>
      </defs>
      <text x="0" y="60" font-family="Anton, sans-serif" font-size="66" fill="#241f2e" textLength="170" lengthAdjust="spacingAndGlyphs">BOLTS</text>
      <text x="0" y="128" font-family="Anton, sans-serif" font-size="66" fill="url(#backRed)" textLength="170" lengthAdjust="spacingAndGlyphs">BURDENS</text>
      <text x="70" y="86" font-family="Anton, sans-serif" font-size="40" fill="#eef2f7" opacity=".9">&amp;</text>
    </svg>
    <p class="back-blurb">Lorem ipsum dolor sit amet, consectetuer adipiscing elit, sed diam nonummy nibh euismod tincidunt ut laoreet dolore magna aliquam erat volutpat. Ut wisi enim ad minim veniam, quis nostrud exerci tation ullamcorper suscipit lobortis nisl ut aliquip ex ea commodo consequat. Duis autem vel eum iriure dolor in hendrerit in vulputate velit esse molestie consequat, vel illum dolore eu feugiat nulla facilisis at vero eros et accumsan et iusto odio dignissim qui blandit praesent luptatum zzril delenit augue duis dolore te feugait nulla facilisi.<br>Lorem ipsum dolor sit amet, cons ectetuer adipiscing elit, sed diam nonummy nibh euismod tincidunt ut laoreet dolore magna aliquam erat volutpat. Ut wisi enim ad minim veniam, quis nostrud exerci tation ullamcorper suscipit lobortis nisl ut aliquip ex ea commodo consequat.</p>
    <div class="byline">WADE PEMBERTON</div>
    <div class="portrait" role="img" aria-label="Author portrait in dress uniform before a flag"></div>
    <p class="bio">Lorem ipsum dolor sit amet, consectetuer adipiscing elit, sed diam nonummy nibh euismod tincidunt ut laoreet dolore magna aliquam erat volutpat. Ut wisi enim ad minim veniam, quis nostrud exerci tation ullamcorper suscipit lobortis nisl ut aliquip ex ea commodo consequat. Duis autem vel eum iriure dolor in hendrerit in vulputate velit esse molestie consequat, vel illum dolore eu feugiat nulla facilisis at vero eros et accumsan et iusto odio dignissim qui blandit praesent luptatum zzril delenit augue duis dolore te feugait</p>
    <div class="band"></div>
  </section>

  <section class="spine">
    <div class="spine-title">BOLTS <span class="red">&amp; BURDENS</span></div>
    <div class="spine-author">WADE PEMBERTON</div>
    <div class="band"></div>
  </section>

  <section class="cover front">
    <svg class="front-title" viewBox="0 0 485 340" aria-label="Bolts &amp; Burdens">
      <defs>
        <linearGradient id="frontRed" x1="0" y1="0" x2="0" y2="1">
          <stop offset="0" stop-color="#2e1f30"/><stop offset=".55" stop-color="#8a1f35"/><stop offset="1" stop-color="#cc1f30"/>
        </linearGradient>
      </defs>
      <text x="0" y="160" font-family="Anton, sans-serif" font-size="170" fill="#241f2e" textLength="485" lengthAdjust="spacingAndGlyphs">BOLTS</text>
      <text x="0" y="335" font-family="Anton, sans-serif" font-size="170" fill="url(#frontRed)" textLength="485" lengthAdjust="spacingAndGlyphs">BURDENS</text>
      <text x="195" y="230" font-family="Anton, sans-serif" font-size="110" fill="#e9eef4" opacity=".88">&amp;</text>
    </svg>
    <div class="subtitle">MENDING WHAT LIES BENEATH</div>
    <div class="flag-haze" role="img" aria-label="Faint waving national flag"></div>
    <div class="hero-jet" role="img" aria-label="Rear view of a K-37 fighter jet parked on the flightline under a blue sky"></div>
    <div class="front-author">WADE PEMBERTON</div>
  </section>

</div>
</body>
</html>
```